New Business Card Design Project LORVANTI-Italy

we are LORVANTI-Italy
our company in the market for 3 years we are luxury cosmetic company and its about time for a facelift :)
i will like to have elegant luxurious and unique business card
that will give the person that get it a unique, luxurious and elegant impression
I'm VERY OPEN FOR NEW IDEAS , even duo i add a few files of things that i see on line and i like them

i add my logo as well
my website is LORVANTI.COM
(if you would like to see the main style that we have)

Target Market(s)

adult that have money :)

Industry/Entity Type

Business

Contact Information for Business Card

Name - Dario Lorvanti
Position - CEO and CO Founder
address - 4817 E Halvern
telephone - 555-384-1926
email - dario@lorvanti.com
fax - 555-384-1926
website - LORVANTI.COM

Colors
000000
959595
fbee3e
ffffff

Requirements
Must have
• big logo in GOLD color
• elegant look
• impressive
Nice to have
• not must but maybe classy pattern background
• not must but maybe emblem
• maybe clear plastic business card
Should not have
• colors
• images

```html
<!DOCTYPE html>
<html lang="en">
<head>
<meta charset="utf-8">
<title>LORVANTI Italy – Business Card</title>
<link rel="stylesheet" href="https://fonts.googleapis.com/css2?family=Open+Sans:wght@400;600;700&display=swap">
<style>
  :root {
    --backdrop: #3a322e;
    --card: #111111;
    --card-edge: #1c1c1c;
    --gold: #d4a94a;
    --gold-light: #f0cf72;
    --white: #ffffff;
    --grey: #959595;
  }
  * { margin: 0; padding: 0; box-sizing: border-box; }
  html, body {
    width: 1200px;
    height: 864px;
    overflow: hidden;
  }
  body {
    background: var(--backdrop);
    font-family: "Open Sans", Arial, sans-serif;
    position: relative;
  }
  .card {
    position: absolute;
    width: 540px;
    height: 309px;
    background: linear-gradient(135deg, var(--card-edge) 0%, var(--card) 60%);
    border-radius: 3px;
    box-shadow: 0 14px 30px rgba(0,0,0,0.45);
    overflow: hidden;
  }
  /* Card back */
  .card-back { left: 60px; top: 100px; }
  .card-back .brand {
    position: absolute;
    left: 0; right: 0;
    top: 108px;
    display: flex;
    align-items: center;
    justify-content: center;
    gap: 14px;
  }
  .brand-dot {
    width: 14px; height: 14px;
    border-radius: 50%;
    background: var(--gold);
  }
  .brand-name {
    color: var(--gold);
    font-weight: 600;
    letter-spacing: 0.12em;
  }
  .card-back .brand-name { font-size: 34px; }
  .card-back .web {
    position: absolute;
    left: 0; right: 0;
    bottom: 34px;
    text-align: center;
    color: var(--grey);
    font-size: 13px;
    letter-spacing: 0.32em;
  }
  /* Card front */
  .card-front { left: 600px; top: 460px; }
  .card-front .brand {
    position: absolute;
    left: 20px;
    width: 240px;
    top: 112px;
    display: flex;
    flex-direction: column;
    align-items: center;
    gap: 12px;
  }
  .card-front .brand-name {
    font-size: 24px;
    text-align: center;
    line-height: 1.2;
  }
  .card-front .brand-name span {
    display: block;
    font-size: 12px;
    letter-spacing: 0.3em;
  }
  .divider {
    position: absolute;
    left: 272px;
    top: 70px;
    width: 1px;
    height: 170px;
    background: linear-gradient(to bottom, transparent, var(--grey), transparent);
  }
  .contact {
    position: absolute;
    left: 294px;
    top: 78px;
    color: var(--white);
  }
  .contact .person {
    color: var(--gold-light);
    font-weight: 700;
    font-size: 18px;
    line-height: 1.1;
  }
  .contact .role {
    font-size: 14px;
    margin-bottom: 12px;
  }
  .contact .address {
    font-size: 12px;
    margin-bottom: 4px;
  }
  .contact ul { list-style: none; }
  .contact li {
    display: flex;
    align-items: center;
    gap: 7px;
    font-size: 12.5px;
    line-height: 1.55;
  }
  .contact svg { width: 11px; height: 11px; fill: var(--gold); flex: none; }
</style>
</head>
<body>

  <section class="card card-back" aria-label="Card back">
    <div class="brand">
      <span class="brand-dot"></span>
      <span class="brand-name">LORVANTI</span>
    </div>
    <p class="web">www.lorvanti.com</p>
  </section>

  <section class="card card-front" aria-label="Card front">
    <div class="brand">
      <span class="brand-dot"></span>
      <p class="brand-name">LORVANTI<span>ITALY</span></p>
    </div>
    <div class="divider"></div>
    <div class="contact">
      <p class="person">Dario Lorvanti</p>
      <p class="role">CEO &amp; CO Founder</p>
      <p class="address">4817 E Halvern</p>
      <ul>
        <li>
          <svg viewBox="0 0 16 16" aria-hidden="true"><path d="M3 1h3l1.5 4-2 1.5a9 9 0 0 0 4 4L11 8.5l4 1.5v3a2 2 0 0 1-2 2A12 12 0 0 1 1 3a2 2 0 0 1 2-2z"/></svg>
          555-384-1926
        </li>
        <li>
          <svg viewBox="0 0 16 16" aria-hidden="true"><path d="M4 1h8v4H4zM1 6h14v6h-3v3H4v-3H1zm4 4v4h6v-4z"/></svg>
          555-384-1926
        </li>
        <li>
          <svg viewBox="0 0 16 16" aria-hidden="true"><path d="M1 3h14v10H1zm1.5 1.5L8 9l5.5-4.5z"/></svg>
          dario@lorvanti.com
        </li>
        <li>
          <svg viewBox="0 0 16 16" aria-hidden="true"><path d="M8 1a7 7 0 1 0 0 14A7 7 0 0 0 8 1zm0 2a5 5 0 0 1 4.9 4H3.1A5 5 0 0 1 8 3zm0 10a5 5 0 0 1-4.9-4h9.8A5 5 0 0 1 8 13z"/></svg>
          LORVANTI.COM
        </li>
      </ul>
    </div>
  </section>

</body>
</html>
```